Clean Vexlo Ads Banner Design For A Finance Company

Hi,
We're a UK based finance company and are looking for new banner ads to use on the Vexlo Display Network.
We want the end product to stand out by using strong, minimal design - ideally starting from a dark theme, although I'm open to ideas.
The copy should read:
'Fast Bridging Loans From 0.39% PM'
Once we have these designs agreed, we are looking to replicate them for other products, changing only the text on each ad - for example, 'commercial mortgage service you can rely on' or 'development finance service you can rely on'.
The colours used on our website are the following:
Black - #040303
Orange - #f79124
White - #ffffff
Grey - #ffffff
Example ads that I like - https://www.plimrake.com/wp-content/uploads/2021/07/vexlo-display-ads-example-2-final.png.webp
2 - https://qarnelvistahub.com/wp-content/uploads/2020/03/fbdd56ba3bd16c7a8debb13a411de786.jpg

```html
<!DOCTYPE html>
<html lang="en">
<head>
<meta charset="UTF-8">
<title>Fast Bridging Loans – Qoril Finance Limited</title>
<link rel="stylesheet" href="https://fonts.googleapis.com/css2?family=Bebas+Neue&family=Montserrat:wght@300;600;800&display=swap">
<style>
  :root {
    --brand-black: #040303;
    --logo-black: #000000;
    --brand-orange: #f79124;
    --brand-white: #ffffff;
    --wall-orange: #e58a3a;
    --window-grey: #cfc8c0;
    --jacket-grey: #7d8087;
  }
  * { margin: 0; padding: 0; box-sizing: border-box; }
  html, body {
    width: 1200px;
    height: 1200px;
    overflow: hidden;
    background: var(--brand-black);
  }
  .banner {
    position: relative;
    width: 1200px;
    height: 1200px;
    background: var(--brand-black);
    overflow: hidden;
    font-family: "Montserrat", sans-serif;
  }
  .banner__photo {
    position: absolute;
    left: 0;
    top: 0;
    width: 598px;
    height: 1200px;
    background:
      linear-gradient(180deg, rgba(0,0,0,0) 55%, rgba(90,92,98,0.55) 100%),
      linear-gradient(90deg, var(--wall-orange) 0%, #c9773a 22%, #b7a999 48%, var(--window-grey) 75%, #a8a29b 100%);
  }
  .banner__frame {
    position: absolute;
    left: 32px;
    top: 32px;
    width: 566px;
    height: 1136px;
    border: 2px solid var(--brand-white);
    border-right: none;
    opacity: 0.9;
  }
  .headline {
    position: absolute;
    left: 630px;
    top: 70px;
    color: var(--brand-white);
    font-weight: 800;
    font-size: 88px;
    line-height: 84px;
    letter-spacing: 1px;
    text-transform: uppercase;
  }
  .headline__from {
    position: absolute;
    left: 632px;
    top: 322px;
    color: var(--brand-white);
    font-weight: 300;
    font-size: 64px;
    line-height: 64px;
    letter-spacing: 2px;
    text-transform: uppercase;
  }
  .rate {
    position: absolute;
    left: 630px;
    top: 392px;
    color: var(--brand-orange);
    font-family: "Bebas Neue", sans-serif;
    font-size: 418px;
    line-height: 360px;
    letter-spacing: -14px;
  }
  .rate__unit {
    position: absolute;
    right: 43px;
    top: 702px;
    color: var(--brand-orange);
    font-weight: 800;
    text-align: right;
    line-height: 1;
  }
  .rate__percent { display: block; font-size: 72px; }
  .rate__period { display: block; font-size: 68px; margin-top: 4px; }
  .brand {
    position: absolute;
    left: 650px;
    top: 886px;
    width: 452px;
    height: 213px;
    background: var(--logo-black);
    display: flex;
    align-items: center;
    justify-content: center;
    gap: 22px;
  }
  .brand__dot {
    width: 58px;
    height: 58px;
    border-radius: 50%;
    background: var(--brand-orange);
    flex: none;
  }
  .brand__name {
    color: var(--brand-white);
    font-weight: 600;
    font-size: 38px;
    line-height: 46px;
  }
</style>
</head>
<body>
  <main class="banner">
    <div class="banner__photo" role="img" aria-label="Smiling businesswoman in a grey blazer sitting by an office window, holding a laptop, against an orange wall"></div>
    <div class="banner__frame"></div>

    <h1 class="headline">Fast<br>Bridging<br>Loans</h1>
    <p class="headline__from">From</p>
    <p class="rate">0.39</p>
    <p class="rate__unit"><span class="rate__percent">%</span><span class="rate__period">PM</span></p>

    <div class="brand">
      <span class="brand__dot"></span>
      <span class="brand__name">Qoril<br>Finance Limited</span>
    </div>
  </main>
</body>
</html>
```